A clean crisp business card for a Landscape Construction company. Designed to be easy to read contact/ info and also be appealing/interesting, unlike a traditional business card.

Industry/Entity Type

Landscape Construction

Contact Information for Business Card

Company name : Brambleford Landscape Construction, phone number: (877) 62Vista, website:Bramblefordyards.example, Email, sales@bramblefordyards.example

Requirements
Nice to have
• Luxurious finishes/ details…. Icons or emblems next to contact info
Should not have
• Clipart or general pictures

```html
<!DOCTYPE html>
<html lang="en">
<head>
<meta charset="utf-8">
<title>Brambleford Landscape Construction – Business Card</title>
<link rel="stylesheet" href="https://fonts.googleapis.com/css2?family=Cinzel:wght@700&family=Cormorant+Garamond:wght@500&display=swap">
<style>
  :root {
    --leaf-green: #9dcb3c;
    --brand-blue: #2367b4;
    --ink: #111111;
    --paper: #ffffff;
    --frame: #1a1a1a;
  }
  html, body {
    margin: 0;
    padding: 0;
    overflow: hidden;
    background: var(--paper);
  }
  .card {
    position: relative;
    width: 1200px;
    height: 728px;
    box-sizing: border-box;
    border-top: 1px solid var(--frame);
    border-left: 1px solid var(--frame);
    background: var(--paper);
    overflow: hidden;
  }
  .brand {
    position: absolute;
    left: 0;
    right: 0;
    top: 150px;
    display: flex;
    flex-direction: column;
    align-items: center;
  }
  .brand-dot {
    width: 90px;
    height: 90px;
    border-radius: 50%;
    background: var(--leaf-green);
    margin-bottom: 26px;
  }
  .brand-name {
    margin: 0;
    font-family: "Cinzel", serif;
    font-weight: 700;
    color: var(--brand-blue);
    text-align: center;
    font-size: 52px;
    line-height: 1.05;
    letter-spacing: 1px;
  }
  .brand-name .tagline {
    display: block;
    font-size: 22px;
    letter-spacing: 5px;
    margin-top: 8px;
  }
  .info-band {
    position: absolute;
    left: 0;
    right: 0;
    bottom: 0;
    height: 254px;
    background: var(--leaf-green);
  }
  .company {
    position: absolute;
    left: 70px;
    top: 58px;
    margin: 0;
    font-family: "Cinzel", serif;
    font-weight: 700;
    color: var(--ink);
    font-size: 40px;
    line-height: 48px;
    letter-spacing: 1.5px;
  }
  .contact-list {
    position: absolute;
    left: 556px;
    top: 54px;
    margin: 0;
    padding: 0;
    list-style: none;
  }
  .contact-item {
    display: flex;
    align-items: center;
    height: 57px;
    font-family: "Cormorant Garamond", serif;
    font-weight: 500;
    font-size: 36px;
    color: var(--ink);
  }
  .contact-icon {
    width: 32px;
    height: 32px;
    flex: none;
    margin-right: 18px;
  }
</style>
</head>
<body>
<main class="card">
  <header class="brand">
    <div class="brand-dot"></div>
    <h1 class="brand-name">Brambleford<span class="tagline">Landscape Construction</span></h1>
  </header>

  <section class="info-band">
    <h2 class="company">Brambleford<br>Landscape<br>Construction</h2>

    <ul class="contact-list">
      <li class="contact-item">
        <svg class="contact-icon" viewBox="0 0 32 32" aria-hidden="true">
          <circle cx="16" cy="16" r="16" fill="var(--brand-blue)"/>
          <path d="M11.5 8.5l2.6 0.2 1.2 3.4-1.7 1.5c0.9 2 2.6 3.7 4.6 4.6l1.5-1.7 3.4 1.2 0.2 2.6c-0.6 1.3-1.9 2-3.3 1.8-5-0.8-8.9-4.7-9.7-9.7-0.2-1.4 0.5-2.7 1.8-3.3z" fill="none" stroke="#fff" stroke-width="1.6" stroke-linejoin="round"/>
        </svg>
        (877) 62Vista
      </li>
      <li class="contact-item">
        <svg class="contact-icon" viewBox="0 0 32 32" aria-hidden="true">
          <circle cx="16" cy="16" r="16" fill="var(--brand-blue)"/>
          <g fill="none" stroke="#fff" stroke-width="1.5">
            <circle cx="16" cy="16" r="8"/>
            <ellipse cx="16" cy="16" rx="3.5" ry="8"/>
            <path d="M8 16h16M9.2 12h13.6M9.2 20h13.6"/>
          </g>
        </svg>
        Bramblefordyards.example
      </li>
      <li class="contact-item">
        <svg class="contact-icon" viewBox="0 0 32 32" aria-hidden="true">
          <circle cx="16" cy="16" r="16" fill="var(--brand-blue)"/>
          <g fill="none" stroke="#fff" stroke-width="1.5" stroke-linejoin="round">
            <rect x="8.5" y="10.5" width="15" height="11"/>
            <path d="M8.5 10.5l7.5 6.5 7.5-6.5M8.5 21.5l5.5-5M23.5 21.5l-5.5-5"/>
          </g>
        </svg>
        sales@bramblefordyards.example
      </li>
    </ul>
  </section>
</main>
</body>
</html>
```